Oil and Gas Exploration and Production company needs a business card design

We need a business card design using our logo and colors in the logo. We want a mainstream design.

```html
<!DOCTYPE html>
<html lang="en">
<head>
<meta charset="utf-8">
<title>Valdera Oil &amp; Gas – Business Card</title>
<link rel="stylesheet" href="https://fonts.googleapis.com/css2?family=Lato:wght@400;700;900&display=swap">
<style>
  :root {
    --canvas: #e6e7e8;
    --card-light: #fbfbfb;
    --card-light-edge: #ededed;
    --ink: #161616;
    --band-top: #3b3b3b;
    --band-bottom: #121212;
    --gold: #c08a2e;
    --gold-light: #d9a548;
    --white: #ffffff;
    --muted: #d8d8d8;
  }
  * { margin: 0; padding: 0; box-sizing: border-box; }
  html, body { width: 1200px; height: 970px; overflow: hidden; }
  body {
    background: var(--canvas);
    font-family: "Lato", Arial, sans-serif;
    position: relative;
  }
  .business-card {
    position: absolute;
    left: 100px;
    top: 186px;
    width: 1000px;
    height: 598px;
    background: linear-gradient(180deg, var(--card-light) 0%, var(--card-light-edge) 100%);
    overflow: hidden;
    box-shadow: 0 18px 40px rgba(0,0,0,0.18);
  }
  .card-wave { position: absolute; inset: 0; width: 100%; height: 100%; }

  .brand { position: absolute; left: 294px; top: 74px; display: flex; align-items: center; gap: 22px; }
  .brand-dot { width: 58px; height: 58px; border-radius: 50%; background: var(--ink); flex: none; }
  .brand-name { color: var(--ink); font-weight: 900; line-height: 1; }
  .brand-name .primary { display: block; font-size: 82px; letter-spacing: -1px; }
  .brand-name .secondary { display: block; font-size: 34px; letter-spacing: 6px; margin-top: 8px; }

  .person { position: absolute; left: 76px; top: 348px; }
  .person-name { color: var(--gold-light); font-weight: 700; font-size: 32px; }
  .person-title { color: var(--white); font-size: 19px; margin-top: 6px; }

  .contact-list { position: absolute; left: 89px; top: 455px; list-style: none; }
  .contact-list li { display: flex; align-items: center; height: 37.5px; font-size: 20px; color: var(--muted); }
  .contact-list svg { width: 20px; height: 20px; margin-right: 18px; flex: none; }
  .contact-list .web { color: var(--gold-light); font-weight: 700; letter-spacing: 1.5px; }

  .address { position: absolute; right: 49px; top: 497px; text-align: right; color: var(--white); font-weight: 700; font-size: 20px; line-height: 34px; }
</style>
</head>
<body>
  <div class="business-card">
    <svg class="card-wave" viewBox="0 0 697 417" preserveAspectRatio="none" aria-hidden="true">
      <defs>
        <linearGradient id="bandFill" x1="0" y1="0" x2="0" y2="1">
          <stop offset="0" stop-color="#3b3b3b"/>
          <stop offset="1" stop-color="#121212"/>
        </linearGradient>
      </defs>
      <path d="M0,252 C90,200 180,170 300,215 C420,262 520,318 640,290 C665,284 685,272 697,258 L697,417 L0,417 Z" fill="url(#bandFill)"/>
      <path d="M0,236 C90,182 180,154 300,198 C420,244 520,298 640,272 C665,266 685,254 697,242" fill="none" stroke="#161616" stroke-width="4"/>
      <path d="M0,245 C90,192 180,164 300,208 C420,254 520,308 640,282 C665,276 685,264 697,250" fill="none" stroke="#c08a2e" stroke-width="5"/>
    </svg>

    <div class="brand">
      <span class="brand-dot"></span>
      <div class="brand-name">
        <span class="primary">Valdera</span>
        <span class="secondary">OIL &amp; GAS</span>
      </div>
    </div>

    <div class="person">
      <p class="person-name">Dana Holloway</p>
      <p class="person-title">Founder &amp; CEO</p>
    </div>

    <ul class="contact-list">
      <li>
        <svg viewBox="0 0 20 20" aria-hidden="true"><path fill="#e8e8e8" d="M5 2h4l1 4-2 1.5a10 10 0 0 0 4.5 4.5L14 10l4 1v4c0 1-1 2-2 2C8.5 17 3 11.5 3 4c0-1 1-2 2-2z"/></svg>
        <span>555.014.2298</span>
      </li>
      <li>
        <svg viewBox="0 0 20 20" aria-hidden="true"><rect x="2" y="4" width="16" height="12" fill="#e8e8e8"/><path d="M2 4l8 7 8-7" fill="none" stroke="#1c1c1c" stroke-width="1.6"/></svg>
        <span>d.holloway@valderaenergy.com</span>
      </li>
      <li>
        <svg viewBox="0 0 20 20" aria-hidden="true"><circle cx="10" cy="10" r="8" fill="none" stroke="#e8e8e8" stroke-width="1.8"/><path d="M2 10h16M10 2c-3 3-3 13 0 16M10 2c3 3 3 13 0 16" fill="none" stroke="#e8e8e8" stroke-width="1.4"/></svg>
        <span class="web">www.valderaenergy.com</span>
      </li>
    </ul>

    <address class="address" style="font-style:normal">
      2180 Harbor View Rd #140<br>
      Palm Crest, Florida 33410
    </address>
  </div>
</body>
</html>
```